Whitcombe Business Card Design

The name of the business is Dario Whitcombe, CPA LLC
The service that we offer is Accounting, Tax & Consulting Services. I need it to have the following items:
Dario Whitcombe, Principal
Phone Number
Email Address
Physical Address

I have attached the company logo, one in black and one in white. Please provide a design in black background and the other in white background. Please include "Accounting, Tax & Consulting Services". I want the business card to be clean and very professional.

```html
<!DOCTYPE html>
<html lang="en">
<head>
<meta charset="utf-8">
<title>Dario Whitcombe, CPA LLC — Business Card</title>
<link rel="stylesheet" href="https://fonts.googleapis.com/css2?family=Montserrat:ital,wght@0,400;0,500;0,600;0,700;1,400&display=swap">
<style>
  :root {
    --backdrop: #b01f24;
    --card: #232021;
    --band: #8f9092;
    --rule: #9a9a9b;
    --text-soft: #a9a9aa;
    --text-muted: #8a8a8b;
    --accent: #a31c20;
    --font: "Montserrat", Arial, sans-serif;
  }
  * { margin: 0; padding: 0; box-sizing: border-box; }
  html, body { width: 1200px; height: 1000px; overflow: hidden; }
  body { background: var(--backdrop); font-family: var(--font); position: relative; }

  .card {
    position: absolute;
    width: 722px;
    background: var(--card);
    overflow: hidden;
  }
  .card__band {
    position: absolute; left: 0; right: 0; bottom: 0; height: 17px;
    background: var(--band);
  }

  /* Front */
  .card--front { left: 410px; top: 89px; height: 400px; }
  .front__rule {
    position: absolute; left: 143px; width: 435px; height: 2px;
    background: var(--rule);
  }
  .front__rule--top { top: 121px; }
  .front__rule--bottom { top: 278px; }
  .brand {
    position: absolute; display: flex; align-items: center; gap: 14px;
    color: var(--text-muted); font-weight: 600; white-space: nowrap;
  }
  .brand__square { background: var(--accent); flex: none; }
  .brand--front { left: 143px; top: 155px; font-size: 24px; }
  .brand--front .brand__square { width: 40px; height: 40px; }
  .front__services {
    position: absolute; left: 143px; width: 435px; top: 226px;
    text-align: center; font-size: 19px; font-weight: 500;
    color: var(--text-soft); letter-spacing: 0.3px;
  }

  /* Back */
  .card--back { left: 87px; top: 535px; height: 403px; }
  .back__flag {
    position: absolute; left: 65px; top: 0; width: 33px; height: 140px;
    background: var(--accent);
  }
  .person__name {
    position: absolute; left: 110px; top: 94px;
    font-size: 26px; font-weight: 500; color: var(--text-soft);
    letter-spacing: 0.5px;
  }
  .person__name strong { font-weight: 700; }
  .person__title {
    position: absolute; left: 110px; top: 126px;
    font-size: 13px; font-style: italic; color: var(--text-muted);
    letter-spacing: 1.5px;
  }
  .person__rule { position: absolute; left: 203px; top: 133px; height: 2px; background: #6e6e6f; width: 118px; }
  .person__rule--light { left: 321px; width: 43px; height: 3px; top: 132px; background: var(--rule); }
  .back__services {
    position: absolute; right: 87px; top: 157px;
    font-size: 13.5px; font-style: italic; color: var(--text-muted);
    letter-spacing: 1px;
  }
  .back__divider { position: absolute; top: 181px; height: 4px; }
  .back__divider--accent { left: 87px; width: 363px; background: var(--accent); height: 3px; top: 182px; }
  .back__divider--grey { left: 450px; width: 185px; background: var(--rule); }

  .contact { position: absolute; left: 82px; width: 243px; height: 36px; }
  .contact__tab { position: absolute; left: 0; top: 0; }
  .contact__text {
    position: absolute; left: 45px; top: 8px;
    font-size: 13px; color: var(--text-soft); letter-spacing: 0.8px;
  }
  .contact--phone { top: 197px; }
  .contact--email { top: 250px; }
  .contact--address { top: 302px; }

  .brand--back { left: 370px; top: 269px; font-size: 14.5px; gap: 10px; }
  .brand--back .brand__square { width: 24px; height: 24px; }
</style>
</head>
<body>

  <section class="card card--front" aria-label="Business card front">
    <div class="front__rule front__rule--top"></div>
    <div class="brand brand--front">
      <span class="brand__square"></span>
      <span class="brand__name">DARIO WHITCOMBE, CPA LLC</span>
    </div>
    <p class="front__services">Accounting, Tax &amp; Consulting Services</p>
    <div class="front__rule front__rule--bottom"></div>
    <div class="card__band"></div>
  </section>

  <section class="card card--back" aria-label="Business card back">
    <div class="back__flag"></div>
    <h1 class="person__name"><strong>DARIO</strong> WHITCOMBE</h1>
    <p class="person__title">PRINCIPAL</p>
    <div class="person__rule"></div>
    <div class="person__rule person__rule--light"></div>
    <p class="back__services">ACCOUNTING, TAX &amp; CONSULTING SERVICES</p>
    <div class="back__divider back__divider--accent"></div>
    <div class="back__divider back__divider--grey"></div>

    <div class="contact contact--phone">
      <svg class="contact__tab" width="243" height="36" viewBox="0 0 243 36">
        <path d="M0 34 V6 Q0 0 6 0 H26 Q32 0 35 8 L38 26 Q41 34 50 34 Z" fill="#8f9092"/>
        <line x1="0" y1="34.5" x2="243" y2="34.5" stroke="#8f9092" stroke-width="1.5"/>
        <path d="M11 9 Q9 10 9.5 13 Q12 22 20 26 Q23 27 24 25 L25 23 Q25 22 24 21.5 L21 20 Q20 19.6 19 20.5 L18 21.5 Q14 19.5 12.5 15.5 L13.5 14.5 Q14.3 13.6 14 12.6 L12.6 9.6 Q12 8.6 11 9 Z" fill="#a31c20"/>
      </svg>
      <span class="contact__text">+111 2222 1111</span>
    </div>

    <div class="contact contact--email">
      <svg class="contact__tab" width="243" height="36" viewBox="0 0 243 36">
        <path d="M0 34 V6 Q0 0 6 0 H26 Q32 0 35 8 L38 26 Q41 34 50 34 Z" fill="#8f9092"/>
        <line x1="0" y1="34.5" x2="243" y2="34.5" stroke="#8f9092" stroke-width="1.5"/>
        <g fill="none" stroke="#a31c20" stroke-width="1.6">
          <circle cx="17" cy="17" r="7.5"/>
          <ellipse cx="17" cy="17" rx="3.3" ry="7.5"/>
          <line x1="9.5" y1="17" x2="24.5" y2="17"/>
          <line x1="11" y1="12.5" x2="23" y2="12.5"/>
          <line x1="11" y1="21.5" x2="23" y2="21.5"/>
        </g>
      </svg>
      <span class="contact__text">info@dariowhitcombe.com</span>
    </div>

    <div class="contact contact--address">
      <svg class="contact__tab" width="243" height="36" viewBox="0 0 243 36">
        <path d="M0 34 V6 Q0 0 6 0 H26 Q32 0 35 8 L38 26 Q41 34 50 34 Z" fill="#8f9092"/>
        <line x1="0" y1="34.5" x2="243" y2="34.5" stroke="#8f9092" stroke-width="1.5"/>
        <path d="M17 24 Q11 17 11 13.5 A6 6 0 0 1 23 13.5 Q23 17 17 24 Z" fill="#a31c20"/>
        <circle cx="17" cy="13.5" r="2.2" fill="#8f9092"/>
        <ellipse cx="17" cy="26" rx="6" ry="1.6" fill="none" stroke="#a31c20" stroke-width="1.3"/>
      </svg>
      <span class="contact__text">Your Address Here 00123</span>
    </div>

    <div class="brand brand--back">
      <span class="brand__square"></span>
      <span class="brand__name">DARIO WHITCOMBE, CPA LLC</span>
    </div>

    <div class="card__band"></div>
  </section>

</body>
</html>
```